Bramblewood Card Company Business Cards

We are a trading card store with Glimmorax, sports and other TCG cards, we need a business card design that encompasses a clean cut, modern style with a retro flare. website is bramblewoodcardco.com for reference. Can utilize a comic book era feel or a more modern outdoor feel to utilize the "Pacific Northwest" elements of tress, mountains, etc.

Industry/Entity Type

Trading cards and collectibles

Contact Information for Business Card

business name, email address, phone number, name, owner job title

Font styles to use
Sans Serif

```html
<!DOCTYPE html>
<html lang="en">
<head>
<meta charset="utf-8">
<title>Bramblewood Card Company – Business Cards</title>
<link href="https://fonts.googleapis.com/css2?family=Montserrat:wght@400;500;700;800&display=swap" rel="stylesheet">
<style>
  :root {
    --teal: #12b2d6;
    --teal-deep: #139ac0;
    --charcoal: #3c3d3f;
    --paper: #f7f7f5;
    --backdrop: #d6d9da;
    --ink: #2e2f31;
    --white: #ffffff;
  }
  * { margin: 0; padding: 0; box-sizing: border-box; }
  html, body {
    width: 1200px; height: 829px; overflow: hidden;
    background: var(--backdrop);
    font-family: "Montserrat", Arial, sans-serif;
  }
  .cards {
    width: 1200px; height: 829px;
    display: flex; align-items: center; justify-content: center; gap: 48px;
  }
  .card {
    position: relative; width: 540px; height: 309px; overflow: hidden;
    box-shadow: 0 10px 28px rgba(0,0,0,0.12);
  }
  .card--front { background: var(--paper); }
  .card--back { background: var(--teal); display: flex; align-items: center; justify-content: center; }

  .band-teal {
    position: absolute; left: 0; top: 108px; width: 360px; height: 108px;
    background: var(--teal-deep);
  }
  .band-charcoal {
    position: absolute; left: 360px; top: 160px; width: 180px; height: 92px;
    background: var(--charcoal);
  }

  .person { position: absolute; left: 34px; top: 38px; }
  .person__name {
    color: var(--teal); font-weight: 800; font-size: 22px; letter-spacing: 1.5px;
    text-transform: uppercase;
  }
  .person__role { color: var(--ink); font-size: 12px; font-weight: 500; margin-top: 2px; }

  .contact {
    position: absolute; left: 34px; top: 120px; color: var(--white);
    font-size: 11.5px; line-height: 17px; list-style: none;
  }
  .contact li { display: flex; align-items: center; gap: 6px; }
  .contact .indent { padding-left: 16px; }
  .contact svg { width: 10px; height: 10px; flex: none; }

  .brand-mark {
    position: absolute; left: 290px; top: 92px; width: 220px; height: 150px;
    background: var(--charcoal); border-radius: 18px;
    display: flex; align-items: center; justify-content: center; text-align: center;
    padding: 0 18px;
  }
  .brand-name {
    color: var(--white); font-weight: 800; font-size: 20px; line-height: 24px;
    letter-spacing: 1px; text-transform: uppercase;
  }
  .card--back .brand-name {
    color: var(--charcoal); font-size: 28px; line-height: 34px; max-width: 300px; text-align: center;
  }
</style>
</head>
<body>
<main class="cards">
  <section class="card card--front" aria-label="Business card front">
    <div class="band-teal"></div>
    <div class="band-charcoal"></div>

    <header class="person">
      <h1 class="person__name">Dorian Kessler</h1>
      <p class="person__role">CEO/Founder</p>
    </header>

    <ul class="contact">
      <li class="indent">P.O. Box 3187 Street</li>
      <li class="indent">Country Name AB 6021</li>
      <li>
        <svg viewBox="0 0 10 10" aria-hidden="true"><path d="M2 0.5 L4 2.6 L3 3.8 Q4.3 6 6.2 7 L7.4 6 L9.5 8 L8 9.5 Q3 9 0.5 2 Z" fill="#fff"/></svg>
        (555) 014 2290
      </li>
      <li>
        <svg viewBox="0 0 10 10" aria-hidden="true"><rect x="0.5" y="2" width="9" height="6.5" fill="#fff"/><path d="M0.5 2 L5 5.5 L9.5 2" stroke="#139ac0" fill="none"/></svg>
        info@bramblewoodcardco.com
      </li>
      <li>
        <svg viewBox="0 0 10 10" aria-hidden="true"><circle cx="5" cy="5" r="4.3" fill="none" stroke="#fff"/><ellipse cx="5" cy="5" rx="1.8" ry="4.3" fill="none" stroke="#fff"/><path d="M0.7 5 H9.3" stroke="#fff"/></svg>
        www.bramblewoodcardco.com
      </li>
    </ul>

    <div class="brand-mark">
      <p class="brand-name">Bramblewood Card Company</p>
    </div>
  </section>

  <section class="card card--back" aria-label="Business card back">
    <p class="brand-name">Bramblewood Card Company</p>
  </section>
</main>
</body>
</html>
```